Design a building access mobile app for Quillo by Tamberlin Entry Systems

Hello, We're looking for an awesome designer to create an app design for our app Quillo, by Tamberlin Entry Systems. the mobile app allows employees open their office doors with their mobile phone. this means they don't have to use those plastic card badges or keys. We like clean modern design, dark and light themes. We don't have a logo yet.
Updates

Reason: Waiting on a couple designers to submit concepts

Target Market(s)

Commercial and employees

Industry/Entity Type

Building

Font styles to use
Sans Serif
Other font styles liked:
• Oswald extra light

Requirements
Must have
• nice clean design

```html
<!DOCTYPE html>
<html lang="en">
<head>
<meta charset="utf-8">
<title>Quillo – Sign Up</title>
<link rel="stylesheet" href="https://fonts.googleapis.com/css2?family=Oswald:wght@200;300;500;700&display=swap">
<style>
  :root {
    --bg-green: #6dff0c;
    --bg-green-soft: #79f52a;
    --deep-green: #4f9a1e;
    --brand-red: #b0162e;
    --field-white: #ffffff;
    --ink: #111111;
    --placeholder: #b4b4b4;
    --faint-text: #a3ef6b;
    --status-ink: #3e7a14;
    --caret: #2f7fe0;
  }
  * { box-sizing: border-box; margin: 0; padding: 0; }
  html, body { width: 675px; height: 1200px; overflow: hidden; }
  body {
    position: relative;
    font-family: "Oswald", "Arial Narrow", sans-serif;
    background: var(--bg-green);
  }
  .backdrop {
    position: absolute; inset: 0;
    background: linear-gradient(160deg, var(--bg-green) 0%, var(--bg-green-soft) 50%, var(--bg-green) 100%);
  }
  .status-bar {
    position: absolute; top: 8px; left: 10px; right: 10px; height: 24px;
    display: flex; align-items: center; justify-content: space-between;
    font-family: "Helvetica Neue", Arial, sans-serif; font-size: 14px; color: var(--status-ink);
  }
  .status-bar .time { position: absolute; left: 50%; transform: translateX(-50%); }
  .status-right { display: flex; align-items: center; gap: 5px; }
  .brand {
    position: absolute; top: 120px; left: 0; right: 0;
    display: flex; flex-direction: column; align-items: center; gap: 40px;
  }
  .brand-square { width: 140px; height: 140px; background: var(--brand-red); }
  .brand-name {
    font-size: 46px; font-weight: 500; color: var(--brand-red); line-height: 1;
  }
  .screen-title {
    position: absolute; top: 458px; left: 0; right: 0; text-align: center;
    font-size: 37px; font-weight: 200; color: var(--deep-green);
  }
  .screen-title span { border-bottom: 1px solid var(--deep-green); line-height: 1.2; }
  .field {
    position: absolute; left: 50px; width: 575px; height: 72px;
    background: var(--field-white); border-radius: 4px;
    box-shadow: 0 2px 2px rgba(0,0,0,0.15);
    display: flex; align-items: center; justify-content: space-between;
    padding: 0 20px 0 23px;
    font-size: 32px; font-weight: 300;
  }
  .field-email { top: 594px; border: 1px solid var(--deep-green); color: var(--ink); }
  .field-password { top: 686px; color: var(--placeholder); }
  .field-confirm { top: 778px; color: var(--placeholder); }
  .caret { display: inline-block; width: 1px; height: 36px; background: var(--caret); vertical-align: middle; margin-left: 4px; }
  .touch-option {
    position: absolute; top: 882px; left: 53px;
    display: flex; align-items: center; gap: 18px;
    font-size: 32px; font-weight: 200; color: var(--deep-green);
  }
  .register-button {
    position: absolute; top: 978px; left: 50px; width: 575px; height: 72px;
    background: var(--deep-green); border-radius: 3px;
    box-shadow: 0 2px 3px rgba(0,0,0,0.2);
    display: flex; align-items: center; justify-content: center;
    font-size: 32px; font-weight: 500; color: #fff;
  }
  .login-prompt {
    position: absolute; top: 1116px; left: 0; right: 0; text-align: center;
    font-size: 29px; font-weight: 200; color: var(--faint-text);
  }
  .login-prompt .login-link { color: var(--deep-green); font-weight: 300; border-bottom: 1px solid var(--deep-green); }
</style>
</head>
<body>
  <div class="backdrop" role="img" aria-label="Faint office hallway photograph washed in bright green"></div>

  <div class="status-bar">
    <div class="status-left">
      <svg width="72" height="14" viewBox="0 0 72 14" aria-hidden="true">
        <g fill="var(--status-ink)">
          <circle cx="5" cy="7" r="4"/><circle cx="15" cy="7" r="4"/><circle cx="25" cy="7" r="4"/><circle cx="35" cy="7" r="4"/><circle cx="45" cy="7" r="4"/>
        </g>
        <path d="M56 5 a10 10 0 0 1 14 0 M59 8 a6 6 0 0 1 8 0" stroke="var(--status-ink)" stroke-width="2" fill="none"/>
        <circle cx="63" cy="11" r="1.6" fill="var(--status-ink)"/>
      </svg>
    </div>
    <div class="time">9:41 PM</div>
    <div class="status-right">
      <span>100%</span>
      <svg width="32" height="14" viewBox="0 0 32 14" aria-hidden="true">
        <rect x="0.5" y="0.5" width="28" height="13" rx="2" fill="none" stroke="var(--status-ink)"/>
        <rect x="2" y="2" width="25" height="10" rx="1" fill="var(--status-ink)"/>
        <rect x="29.5" y="4.5" width="2" height="5" fill="var(--status-ink)"/>
      </svg>
    </div>
  </div>

  <header class="brand">
    <div class="brand-square"></div>
    <div class="brand-name">Tamberlin Entry</div>
  </header>

  <h1 class="screen-title"><span>Sign Up</span></h1>

  <div class="field field-email">
    <span>janerowe@example.com<span class="caret"></span></span>
    <svg width="36" height="28" viewBox="0 0 36 28" aria-hidden="true">
      <rect x="1" y="1" width="34" height="26" fill="var(--deep-green)"/>
      <path d="M2 3 L18 16 L34 3 M2 26 L14 14 M34 26 L22 14" stroke="#fff" stroke-width="2.5" fill="none"/>
    </svg>
  </div>

  <div class="field field-password">
    <span>Password</span>
    <svg width="30" height="40" viewBox="0 0 30 40" aria-hidden="true">
      <path d="M7 17 V11 a8 8 0 0 1 16 0 V17" stroke="var(--deep-green)" stroke-width="4" fill="none"/>
      <rect x="1" y="16" width="28" height="23" rx="3" fill="var(--deep-green)"/>
      <circle cx="15" cy="25" r="3" fill="#fff"/><rect x="13.8" y="25" width="2.4" height="7" fill="#fff"/>
    </svg>
  </div>

  <div class="field field-confirm">
    <span>Confirm Password</span>
    <svg width="30" height="40" viewBox="0 0 30 40" aria-hidden="true">
      <path d="M7 17 V11 a8 8 0 0 1 16 0 V17" stroke="var(--deep-green)" stroke-width="4" fill="none"/>
      <rect x="1" y="16" width="28" height="23" rx="3" fill="var(--deep-green)"/>
      <circle cx="15" cy="25" r="3" fill="#fff"/><rect x="13.8" y="25" width="2.4" height="7" fill="#fff"/>
    </svg>
  </div>

  <div class="touch-option">
    <svg width="34" height="34" viewBox="0 0 34 34" aria-hidden="true">
      <rect x="1.5" y="1.5" width="31" height="31" rx="3" fill="none" stroke="var(--deep-green)" stroke-width="2.5"/>
      <path d="M8 17 L14 24 L27 9" stroke="var(--deep-green)" stroke-width="2.5" fill="none"/>
    </svg>
    <span>Enable Touch</span>
  </div>

  <div class="register-button">Register</div>

  <p class="login-prompt">Already have an account? <span class="login-link">LOGIN</span> now</p>
</body>
</html>
```